Business Card Design

We are a company that provides stump grinding services for residential and commercial clients. Looking for a simple business card design that may have some type of graphic on the card that will tie in with the Tamsen name(Grizzly Bear, Paw Print, etc) . Possibly some foliage wrapping around part of the card? Would like to have a simple design that stands out because it is unique. We are working on getting the website set up and there is a simple graphic on the top of the page that came to mind when I mentioned the leaves.

Industry/Entity Type

Business

Contact Information for Business Card

Tamsen Stump Grinding 303-257-4788KodiakStumps.Com

Font styles to use
Serif

Requirements
Must have
• Business name
• Website Address
• Phone Number
Nice to have
• Graphics that would be associated with a Tamsen bear.
Should not have
• Nothing frilly

```html
<!DOCTYPE html>
<html lang="en">
<head>
<meta charset="utf-8">
<title>Tamsen Stump Grinding — Business Card</title>
<link rel="stylesheet" href="https://fonts.googleapis.com/css2?family=Cinzel:wght@400;500&family=PT+Sans:wght@400&display=swap">
<style>
  :root {
    --stage: #000000;
    --card: #2f3034;
    --ink: #f2f2f2;
    --ink-muted: #8a8a8e;
    --rule: #45464b;
    --icon: #b9b9bc;
  }
  * { margin: 0; padding: 0; box-sizing: border-box; }
  html, body {
    width: 1200px; height: 900px; overflow: hidden;
    background: var(--stage);
  }
  .stage { position: relative; width: 1200px; height: 900px; }
  .card {
    position: absolute; top: 271px;
    width: 456px; height: 281px;
    background: var(--card);
    border-radius: 14px;
  }
  .card--back { left: 137px; }
  .card--front { left: 627px; }

  .brand-name {
    position: absolute;
    font-family: "Cinzel", serif;
    font-weight: 500;
    color: var(--ink);
    white-space: nowrap;
  }
  .card--back .brand-name {
    left: 130px; top: 139px; transform: translate(-50%, -50%);
    font-size: 30px; letter-spacing: 1px;
  }
  .divider {
    position: absolute; left: 231px; top: 94px;
    width: 1px; height: 92px; background: var(--rule);
  }
  .contact {
    position: absolute; left: 250px; top: 120px;
    list-style: none;
    font-family: "PT Sans", sans-serif;
    font-size: 13px; color: var(--ink);
  }
  .contact li { display: flex; align-items: center; height: 20px; }
  .contact svg { width: 11px; height: 11px; margin-right: 13px; fill: none; stroke: var(--icon); stroke-width: 1.5; }
  .contact .icon-phone { fill: var(--icon); stroke: none; }

  .card--front .brand-name {
    left: 50%; top: 107px; transform: translate(-50%, -50%);
    font-size: 36px; letter-spacing: 1px;
  }
  .company {
    position: absolute; left: 0; width: 100%; text-align: center;
    font-family: "Cinzel", serif; white-space: nowrap;
  }
  .company__line1 { top: 152px; font-size: 29px; color: var(--ink); letter-spacing: 0.5px; }
  .company__line2 { top: 188px; font-size: 23px; color: var(--ink-muted); letter-spacing: 12px; padding-left: 12px; }
</style>
</head>
<body>
<main class="stage">
  <section class="card card--back" aria-label="Card back with contact details">
    <div class="brand-name">Tamsen</div>
    <div class="divider"></div>
    <ul class="contact">
      <li>
        <svg viewBox="0 0 12 12" aria-hidden="true"><path class="icon-phone" d="M1 3.5C1 2 3 1.5 6 1.5S11 2 11 3.5V5H8.5V4H3.5V5H1Z M2.5 6H9.5L10.5 10.5H1.5Z"/></svg>
        303-555-0146
      </li>
      <li>
        <svg viewBox="0 0 12 12" aria-hidden="true"><path d="M5 7 L7 5 M4.5 5.5 L2.8 7.2 a1.7 1.7 0 0 0 2.4 2.4 L6.5 8.3 M7.5 6.5 L9.2 4.8 a1.7 1.7 0 0 0 -2.4 -2.4 L5.5 3.7"/></svg>
        TamsenStumps.Com
      </li>
    </ul>
  </section>

  <section class="card card--front" aria-label="Card front">
    <div class="brand-name">Tamsen</div>
    <div class="company company__line1">Tamsen Stump</div>
    <div class="company company__line2">Grinding</div>
  </section>
</main>
</body>
</html>
```